Create a premium soap bar box bar design for an all-natural, men's skincare brand.

We are launching a men’s premium, natural soap bar and skincare business. To start, we will be launching cold-press, all-natural soap bars with a few additional products such as lotions. We plan to expand our line into additional skincare products such as face exfoliants, moisturizers and cleansers that target basic needs such as anti-aging, clarifying and hydrating.

Our target audience is men ages 25-50, with a secondary audience of male teens. Our target audience are mid to high income, professionals that live in more urban areas, but enjoy being active outdoors after work and on the weekends. Our target audience are hard workers, humble and want to enjoy all that life has to offer – whether that’s on top of a mountain or an ocean wave. They hike, bike, skateboard, surf or any other sport that gets them outside. They are husbands, brothers and fathers – there for their family and friends.

Our brand is sophisticated, adventurous and has a sense of humor. Many of our competitors either focus on the rugged outdoors or are more pretentious. We are in-between. We are free spirited and love the fresh air. Our products are trustworthy with no toxic chemicals or harsh ingredients. We are all-natural and provide high-quality, premium products that our audience expects and deserves.

Target Market(s)

Men, ages 25-54 who are high-earning professionals, yet enjoy getting outdoors and being active on the weekends - hiking, biking, surfing, skateboarding and more.

Industry/Entity Type

Men's skincare

Font styles to use
Sans Serif

Requirements
Must have
• See attachments
Nice to have
• We would prefer to a have a premium, slightly more modern looking design that will appeal to our target audience and slightly higher price point.
Should not have
• Please do not include an icon for the fragrance, i.e. cinnamon sticks. However, we do need some differentiation for the fragrance, i.e. color, etc. as it will be on the shelf with other fragrances.

```html
<!DOCTYPE html>
<html lang="en">
<head>
<meta charset="utf-8">
<title>Hale Ridge – Cinnamon Bark Soap Box</title>
<link rel="stylesheet" href="https://fonts.googleapis.com/css2?family=Fredoka:wght@400;500;600;700&display=swap">
<style>
  :root {
    --bg: #d9d8d6;
    --red-deep: #6e0f12;
    --red-mid: #9c161b;
    --red-bright: #c2232a;
    --navy: #1f3c66;
    --cream: #f3e7b5;
    --cream-light: #f8efc6;
    --pink: #f08a7e;
    --logo-red: #c62a2a;
  }
  * { margin: 0; padding: 0; box-sizing: border-box; }
  html, body {
    width: 1200px; height: 675px; overflow: hidden;
    background: var(--bg);
    font-family: "Fredoka", sans-serif;
  }
  .canvas {
    position: relative; width: 1200px; height: 675px;
    display: flex; justify-content: center; align-items: center;
  }
  .box { display: flex; height: 560px; box-shadow: 0 18px 40px rgba(0,0,0,.25); }

  .woodgrain {
    background:
      linear-gradient(180deg,
        var(--red-mid) 0%, var(--red-bright) 8%, var(--red-deep) 14%,
        var(--red-bright) 22%, var(--red-mid) 30%, var(--red-deep) 36%,
        var(--red-bright) 46%, var(--red-mid) 55%, var(--red-deep) 62%,
        var(--red-bright) 72%, var(--red-mid) 82%, var(--red-deep) 90%,
        var(--red-mid) 100%);
  }

  /* side panel */
  .side-panel {
    position: relative; width: 170px; height: 100%;
    border-right: 1px solid rgba(0,0,0,.25);
  }
  .side-copy {
    position: absolute; left: 14px; top: 40px; height: 420px;
    writing-mode: vertical-rl; transform: rotate(180deg);
    display: flex; gap: 4px; text-transform: uppercase;
  }
  .directions {
    font-weight: 700; font-size: 36px; line-height: 1.05; letter-spacing: .5px;
    color: var(--navy);
    -webkit-text-stroke: 6px var(--cream); paint-order: stroke fill;
  }
  .site-note {
    font-weight: 600; font-size: 12px; letter-spacing: .3px;
    color: var(--navy);
    -webkit-text-stroke: 3px var(--cream); paint-order: stroke fill;
  }
  .side-brand {
    position: absolute; bottom: 26px; left: 16px;
    display: flex; align-items: center; gap: 5px;
    background: var(--cream); padding: 3px 8px; border-radius: 3px;
  }
  .side-brand .mark-dot { width: 12px; height: 12px; border-radius: 50%; background: var(--logo-red); }
  .side-brand span { font-weight: 500; font-size: 13px; color: var(--navy); text-transform: uppercase; }

  /* front panel */
  .front-panel {
    position: relative; width: 420px; height: 100%;
    display: flex; flex-direction: column;
  }
  .front-art { flex: 1; display: flex; flex-direction: column; align-items: center; justify-content: center; padding-bottom: 30px; }
  .product-name {
    text-align: center; text-transform: uppercase; color: var(--navy);
    -webkit-text-stroke: 10px var(--cream); paint-order: stroke fill;
    line-height: .95; font-weight: 700;
  }
  .product-name .scent { display: block; font-size: 46px; font-weight: 600; letter-spacing: 1px; }
  .product-name .note { display: block; font-size: 92px; letter-spacing: 1px; }
  .product-type {
    margin-top: 10px; display: flex; align-items: center; gap: 6px;
    font-weight: 600; font-size: 17px; text-transform: uppercase; color: var(--pink);
    -webkit-text-stroke: 5px var(--cream); paint-order: stroke fill;
  }
  .product-type .bullet { width: 10px; height: 10px; border-radius: 50%; border: 2px solid var(--pink); background: var(--cream); }
  .brand-band {
    height: 108px; background: var(--cream-light);
    display: flex; align-items: center; justify-content: center; gap: 12px;
  }
  .brand-band .mark-dot { width: 40px; height: 40px; border-radius: 50%; border: 3px solid var(--logo-red); }
  .brand-band span { font-weight: 500; font-size: 32px; color: var(--navy); text-transform: uppercase; letter-spacing: 1px; }
</style>
</head>
<body>
<main class="canvas">
  <div class="box">
    <section class="side-panel woodgrain" role="img" aria-label="Red cinnamon wood-grain texture">
      <div class="side-copy">
        <p class="directions">Directions: Lather,<br>Rinse and repeat.</p>
        <p class="site-note">Check out all our products at haleridge.com</p>
      </div>
      <div class="side-brand"><i class="mark-dot"></i><span>Hale Ridge</span></div>
    </section>
    <section class="front-panel woodgrain" role="img" aria-label="Red cinnamon wood-grain texture">
      <div class="front-art">
        <h1 class="product-name"><span class="scent">Cinnamon</span><span class="note">Bark</span></h1>
        <p class="product-type"><i class="bullet"></i>Men's Natural Soap</p>
      </div>
      <div class="brand-band"><i class="mark-dot"></i><span>Hale Ridge</span></div>
    </section>
  </div>
</main>
</body>
</html>
```